Quiet Harbor, Weekly therapy lessons for the heart of a sister missionary

This is a weekly guided therapy book for female Mormon missionaries. They leave for their missions for 18 months and I am a psychotherapist that is creating a guided workbook to help them through mental health struggles on their mission. I need a good book cover, also preferably something for the spine and back as well. I would like something that gives a soft and safe feeling.

```html
<!DOCTYPE html>
<html lang="en">
<head>
<meta charset="utf-8">
<title>Quiet Harbor – Book Cover</title>
<link rel="stylesheet" href="https://fonts.googleapis.com/css2?family=Crimson+Pro:wght@400;500;600&family=Cormorant+Garamond:wght@500&display=swap">
<style>
  :root {
    --backdrop: #ece8dc;
    --paper: #fdfbf0;
    --gold: #8a7238;
    --terracotta: #e0a08c;
    --blush: #f1d2c2;
    --sage: #b7c6b3;
  }
  * { margin: 0; padding: 0; box-sizing: border-box; }
  html, body {
    width: 1200px;
    height: 1200px;
    overflow: hidden;
    background: var(--backdrop);
  }
  .cover {
    position: absolute;
    left: 200px;
    top: 0;
    width: 800px;
    height: 1200px;
    background: var(--paper);
    color: var(--gold);
    text-align: center;
  }
  .cover-title {
    position: absolute;
    top: 112px;
    left: 0;
    width: 100%;
    font-family: "Crimson Pro", serif;
    font-weight: 500;
    font-size: 120px;
    letter-spacing: -3px;
    line-height: 1;
  }
  .cover-subtitle {
    position: absolute;
    top: 292px;
    left: 0;
    width: 100%;
    font-family: "Crimson Pro", serif;
    font-weight: 400;
    font-size: 35px;
    line-height: 47px;
  }
  .cover-illustration {
    position: absolute;
    top: 440px;
    left: 0;
    width: 800px;
    height: 490px;
    background: linear-gradient(160deg, var(--terracotta) 0%, var(--blush) 45%, var(--sage) 100%);
    -webkit-mask-image: linear-gradient(180deg, transparent 0%, #000 25%, #000 85%, transparent 100%);
    mask-image: linear-gradient(180deg, transparent 0%, #000 25%, #000 85%, transparent 100%);
  }
  .cover-author {
    position: absolute;
    top: 1083px;
    left: 0;
    width: 100%;
    font-family: "Cormorant Garamond", serif;
    font-weight: 500;
    font-size: 42px;
    letter-spacing: 8px;
    line-height: 1;
  }
</style>
</head>
<body>
  <main class="cover">
    <h1 class="cover-title">Quiet Harbor</h1>
    <p class="cover-subtitle">Weekly therapy lessons for<br>the heart of a sister missionary</p>
    <div class="cover-illustration" role="img" aria-label="Watercolour landscape of rolling terracotta and sage hills with a winding light path, a gold line-drawn heart and a rising sun"></div>
    <p class="cover-author">AUTHOR NAME</p>
  </main>
</body>
</html>
```